Business Cards - Brightpath Horizon

need to design unique business card for my mortgage business. I need to design credit card style business card for my business or any unique idea that you might have

Target Market(s)

Home Loan customers

Industry/Entity Type

Mortgage Brokerage

Contact Information for Business Card

please design credit card style or very unique style business card

Colors

Designer to choose colors to be used in the design.

Requirements
Must have
• Name
• position
• Phone number
• fax number
• email address
• website address
• social media address
• All above fields will be provided once design in finalised

```html
<!DOCTYPE html>
<html lang="en">
<head>
<meta charset="UTF-8">
<title>Brightpath Horizon – Business Card</title>
<link href="https://fonts.googleapis.com/css2?family=Roboto+Slab:wght@700&family=Share+Tech+Mono&family=Open+Sans:wght@400;700&display=swap" rel="stylesheet">
<style>
  :root {
    --page-bg: #d9d6d2;
    --card-bg: #fbfbfa;
    --brand-blue: #1a3fc4;
    --number-blue: #1230d6;
    --accent-orange: #f7931e;
    --text-grey: #4a4a4a;
  }
  * { margin: 0; padding: 0; box-sizing: border-box; }
  html, body {
    width: 1200px;
    height: 969px;
    overflow: hidden;
    background: var(--page-bg);
  }
  .business-card {
    position: absolute;
    left: 100px;
    top: 200px;
    width: 1000px;
    height: 570px;
    background: var(--card-bg);
    border-radius: 4px;
    box-shadow: 0 2px 10px rgba(0,0,0,0.12);
  }
  .holder {
    position: absolute;
    right: 53px;
    top: 40px;
    text-align: right;
    font-family: "Roboto Slab", serif;
    font-weight: 700;
  }
  .holder-name {
    color: var(--brand-blue);
    font-size: 34px;
    line-height: 1.2;
    letter-spacing: 0.5px;
  }
  .holder-role {
    color: var(--accent-orange);
    font-size: 25px;
    line-height: 1.2;
    letter-spacing: 0.5px;
  }
  .card-number {
    position: absolute;
    left: 62px;
    top: 238px;
    font-family: "Share Tech Mono", monospace;
    font-size: 68px;
    color: var(--number-blue);
    letter-spacing: 10px;
    word-spacing: 24px;
    white-space: nowrap;
  }
  .brand {
    position: absolute;
    left: 58px;
    top: 360px;
    width: 200px;
    font-family: "Roboto Slab", serif;
    font-weight: 700;
    font-size: 30px;
    line-height: 1.1;
    color: var(--brand-blue);
  }
  .social-links {
    position: absolute;
    left: 58px;
    top: 478px;
    display: flex;
    gap: 8px;
  }
  .social-links svg { display: block; }
  .contact-list {
    position: absolute;
    left: 308px;
    top: 392px;
    list-style: none;
    font-family: "Open Sans", sans-serif;
    font-size: 23px;
    line-height: 32px;
    color: var(--text-grey);
  }
  .contact-label {
    color: var(--brand-blue);
    font-weight: 700;
    margin-right: 6px;
  }
</style>
</head>
<body>
  <div class="business-card">
    <div class="holder">
      <div class="holder-name">DANIEL REYES</div>
      <div class="holder-role">CEO/FOUNDER</div>
    </div>

    <div class="card-number">614 272 0390</div>

    <div class="brand">Brightpath Horizon</div>

    <div class="social-links" aria-label="Social media links">
      <svg width="44" height="44" viewBox="0 0 44 44"><circle cx="22" cy="22" r="22" fill="var(--brand-blue)"/></svg>
      <svg width="44" height="44" viewBox="0 0 44 44"><circle cx="22" cy="22" r="22" fill="var(--brand-blue)"/></svg>
      <svg width="44" height="44" viewBox="0 0 44 44"><circle cx="22" cy="22" r="22" fill="var(--brand-blue)"/></svg>
      <svg width="44" height="44" viewBox="0 0 44 44"><circle cx="22" cy="22" r="22" fill="var(--brand-blue)"/></svg>
    </div>

    <ul class="contact-list">
      <li><span class="contact-label">P.</span>614 272 0385</li>
      <li><span class="contact-label">F.</span>614 272 0390</li>
      <li><span class="contact-label">E.</span>hello@brightpath.com</li>
      <li><span class="contact-label">W.</span>www.brightpath.com</li>
    </ul>
  </div>
</body>
</html>
```